Business Card Design needed for start up company Halvora

In need of a new business card designed for a start up company based in Sydney, Halvora is a new start up innovative Company, our mission it to make property accessible for everyday Australian and to become the leading Real Estate platform in Australia. We want it to be fresh and clean.

Industry/Entity Type

Financial

Contact Information for Business Card

Section for Name
Section for Title

HALVORA - The Strength of Pooling
Mobile:
Direct:

Font styles to use
Sans Serif

Colors
33a6d7
0692cd
0255a3
ffffff

Requirements
Must have
• Logo, all business card details

```html
<!DOCTYPE html>
<html lang="en">
<head>
<meta charset="utf-8">
<title>Halvora Business Card</title>
<link rel="stylesheet" href="https://fonts.googleapis.com/css2?family=Jost:wght@400;500;600;700&display=swap">
<style>
  :root {
    --navy: #1e3a6e;
    --sky: #33a6d7;
    --sky-deep: #249bd6;
    --white: #ffffff;
    --paper: #f3f3f3;
    --backdrop: #e6e4e1;
  }
  * { margin: 0; padding: 0; box-sizing: border-box; }
  html, body { width: 1200px; height: 960px; overflow: hidden; }
  body {
    position: relative;
    background: var(--backdrop);
    font-family: "Jost", Arial, sans-serif;
  }
  .card {
    position: absolute;
    width: 600px;
    height: 343px;
    border-radius: 22px;
    overflow: hidden;
    box-shadow: 0 4px 10px rgba(0,0,0,0.25);
  }
  .card-front { left: 216px; top: 131px; background: var(--navy); }
  .card-back { left: 381px; top: 504px; background: var(--sky-deep); }
  .front-shape { position: absolute; inset: 0; }

  .contact { position: absolute; left: 44px; top: 86px; color: var(--white); }
  .contact-name {
    font-size: 21px; font-weight: 600; color: var(--sky);
    letter-spacing: 0.3px; line-height: 1.1;
  }
  .contact-title { font-size: 15px; font-weight: 400; line-height: 1.3; }
  .contact-address { margin-top: 14px; font-size: 14px; line-height: 1.3; }
  .contact-list { margin-top: 13px; list-style: none; font-size: 14px; line-height: 1.4; }
  .contact-list li { display: flex; align-items: center; gap: 9px; }
  .contact-list svg { width: 12px; height: 12px; fill: var(--sky); flex: none; }

  .brand { position: absolute; display: flex; align-items: center; white-space: nowrap; }
  .brand-dot { border-radius: 50%; flex: none; }
  .brand-name { font-weight: 700; line-height: 1; }
  .brand-front { left: 311px; top: 140px; gap: 8px; }
  .brand-front .brand-dot { width: 70px; height: 70px; background: var(--sky); }
  .brand-front .brand-name { font-size: 36px; color: var(--navy); }
  .brand-back { left: 122px; top: 116px; gap: 10px; }
  .brand-back .brand-dot { width: 104px; height: 104px; background: var(--white); }
  .brand-back .brand-name { font-size: 52px; color: var(--white); }

  .tagline {
    position: absolute; left: 0; right: 0; top: 284px;
    text-align: center; color: var(--white); font-size: 16px;
  }
</style>
</head>
<body>
  <section class="card card-front">
    <svg class="front-shape" viewBox="0 0 600 343" aria-hidden="true">
      <path d="M404 0 A175 175 0 0 0 419 343 L600 343 L600 0 Z" fill="var(--sky)"/>
      <path d="M410 0 A175 175 0 0 0 425 343 L600 343 L600 0 Z" fill="var(--paper)"/>
    </svg>
    <div class="contact">
      <p class="contact-name">MARA LEATON</p>
      <p class="contact-title">CEO/FOUNDER</p>
      <p class="contact-address">214 Wattle Crescent<br>Surry Hills, NSW 2010</p>
      <ul class="contact-list">
        <li><svg viewBox="0 0 12 12"><path d="M2.5 0.5l2 2.3-1.1 1.6c.7 1.6 1.9 2.9 3.6 3.7l1.5-1.1 2.4 2-1 2.2C5.4 10.9 1 6.6.5 2.1z"/></svg>02 8193 4476</li>
        <li><svg viewBox="0 0 12 12"><path d="M3 0h6a1 1 0 0 1 1 1v10a1 1 0 0 1-1 1H3a1 1 0 0 1-1-1V1a1 1 0 0 1 1-1zm.5 1.5v8h5v-8z"/></svg>0412 557 308</li>
        <li><svg viewBox="0 0 12 12"><path d="M0 2.5h12v7H0zM.8 3.2 6 7l5.2-3.8v-.1H.8z"/></svg>mara@halvora.com</li>
        <li><svg viewBox="0 0 12 12"><circle cx="6" cy="6" r="5.5"/></svg>www.halvora.com</li>
      </ul>
    </div>
    <div class="brand brand-front">
      <span class="brand-dot"></span>
      <span class="brand-name">HALVORA</span>
    </div>
  </section>

  <section class="card card-back">
    <div class="brand brand-back">
      <span class="brand-dot"></span>
      <span class="brand-name">HALVORA</span>
    </div>
    <p class="tagline">The Strength of Pooling</p>
  </section>
</body>
</html>
```